Business Card design for insurance broker in Denver, CO, USA

I need a business card designed using this logo that was just created. We sell life and disability income insurance to US consumers.
Looking for a professionally designed card to make use of the logo and have something to hand to prospects or new business referral sources. The card could be white, gray, black or whatever you would recommend.

Target Market(s)

US Consumers and other financial professionals that I partner with.

Industry/Entity Type

Insurance Broker

Contact Information for Business Card

Owen T. Farrow, CLU, LUTCF (please note that CLU should have a superscript R in a circle for registered trademark)
President
phone (303) 555-0187
email owen@keelbrookcover.example
4620 W. Halvern Rd, Suite 300, Greenwood Village, CO 80111
Somewhere fit in a tagline saying "Your resource for life, long term care, and disability insurance" (maybe the back if it doesn't fit on the front, your call)

Font styles to use
Sans Serif

Requirements
Must have
• Must have logo in correct blue and gray colors, my name, address, phone, email. Order and placement determined by the designer.
• I just want something that looks a more professional than what I could have done using the business card designer tool on pixelbazaar.example or QuillPress, or any other do-it-yourself tool
• A regular rectangular business card with square corners is preferred
Nice to have
• I included the logos of 2 organizations I belong to (GKLS and WOBCE). They should be small, but visible on the back only. If it doesn’t look good, this is not a requirement, feel free to drop it.
Should not have
• Do not add any colors not already in the logo, except use of black and whites which are okay. If you use the logo on the back and want to make that in all black, gray or white, that may be okay as well.

```html
<!DOCTYPE html>
<html lang="en">
<head>
<meta charset="utf-8">
<title>Keelbrook Cover – Business Card</title>
<link href="https://fonts.googleapis.com/css2?family=Roboto:ital,wght@0,300;0,400;0,500;0,700;1,300;1,400&display=swap" rel="stylesheet">
<style>
  :root {
    --blue: #0a86cf;
    --band-blue: #0f88d2;
    --rule-blue: #1d5fae;
    --gray: #9a9a9a;
    --text-gray: #7a7a7a;
    --divider: #a8a8a8;
    --card: #ffffff;
    --backdrop: #e9eaec;
  }
  * { margin: 0; padding: 0; box-sizing: border-box; }
  html, body { width: 1125px; height: 1200px; overflow: hidden; }
  body {
    background: var(--backdrop);
    font-family: "Roboto", Arial, sans-serif;
    position: relative;
  }
  .card {
    position: absolute;
    left: 150px;
    width: 824px;
    height: 470px;
    background: var(--card);
    box-shadow: 0 2px 10px rgba(0,0,0,0.12);
    overflow: hidden;
  }
  .card-front { top: 98px; }
  .card-back { top: 630px; }

  /* front */
  .identity {
    position: absolute;
    right: 428px;
    top: 198px;
    text-align: right;
  }
  .identity .name {
    color: var(--blue);
    font-weight: 700;
    font-size: 22px;
    letter-spacing: 0.2px;
    white-space: nowrap;
  }
  .identity .name .creds { font-size: 17px; }
  .identity .name sup { font-size: 13px; }
  .identity .role {
    color: var(--gray);
    font-weight: 700;
    font-size: 19px;
    margin-top: 4px;
  }
  .divider {
    position: absolute;
    left: 419px;
    top: 166px;
    width: 1px;
    height: 131px;
    background: var(--divider);
  }
  .contact {
    position: absolute;
    left: 442px;
    top: 160px;
    color: var(--text-gray);
    font-weight: 300;
    font-size: 19px;
    line-height: 25.5px;
  }
  .contact .address { margin-bottom: 8px; }
  .tagline-band {
    position: absolute;
    left: 0; right: 0;
    top: 396px;
    height: 40px;
    background: var(--band-blue);
    color: #fff;
    font-style: italic;
    font-size: 17.5px;
    font-weight: 300;
    display: flex;
    align-items: center;
    justify-content: center;
  }
  .tagline-band strong { font-weight: 400; margin-left: 5px; }

  /* back */
  .brand {
    position: absolute;
    left: 0; right: 0;
    top: 140px;
    display: flex;
    align-items: center;
    justify-content: center;
    gap: 22px;
  }
  .brand-mark {
    width: 118px; height: 118px;
    border: 7px solid var(--blue);
    border-radius: 50%;
  }
  .brand-name {
    color: var(--blue);
    font-weight: 500;
    font-size: 46px;
    line-height: 1;
    letter-spacing: 0.5px;
  }
  .member-rule {
    position: absolute;
    left: 0; right: 0;
    top: 405px;
    height: 5px;
    background: var(--rule-blue);
  }
  .badges {
    position: absolute;
    top: 368px;
    left: 312px;
    display: flex;
    gap: 22px;
    align-items: flex-end;
  }
  .badge-association {
    width: 90px; height: 54px;
    background: #2c62ad;
  }
  .badge-roundtable {
    width: 66px; height: 66px;
    border-radius: 50%;
    background: #7ea6d6;
  }
</style>
</head>
<body>
  <section class="card card-front">
    <div class="identity">
      <div class="name">OWEN T. FARROW, <span class="creds">CLU<sup>®</sup>, LUTCF</span></div>
      <div class="role">CEO/FOUNDER</div>
    </div>
    <div class="divider"></div>
    <div class="contact">
      <div class="address">4620 W. Halvern Rd, Suite 300<br>Lakeridge Springs, CO 80999</div>
      <div>(303) 555-0187</div>
      <div>owen@keelbrookcover.example</div>
      <div>www.keelbrookcover.example</div>
    </div>
    <div class="tagline-band">Your resource for <strong>life, long term care, &amp; disability insurance</strong></div>
  </section>

  <section class="card card-back">
    <div class="brand">
      <div class="brand-mark"></div>
      <div class="brand-name">KEELBROOK COVER</div>
    </div>
    <div class="member-rule"></div>
    <div class="badges">
      <div class="badge-association" role="img" aria-label="Professional association membership badge"></div>
      <div class="badge-roundtable" role="img" aria-label="Roundtable membership badge"></div>
    </div>
  </section>
</body>
</html>
```